Modern Verdell Tree Care Website

I need a website for a full service Tree Care company. The company provides tree pruning, tree removal, tree preservation, emergency services, stump grinding, and emergency tree services.

Target Market(s)

Customers that need tree services

Industry/Entity Type

Landscaping, Tree Services

Coding

Coded - Design and coding required

Number of Pages Required

5+ page

Font styles to use
Sans Serif

Requirements
Must have
• Good clean design that showcases the services the company provides.
Nice to have
• Services page; contact form, blog, home page, about page

```html
<!DOCTYPE html>
<html lang="en">
<head>
<meta charset="utf-8">
<title>Verdell Tree Care</title>
<link href="https://fonts.googleapis.com/css2?family=Lato:wght@400;700&family=Michroma&family=Oswald:wght@500&display=swap" rel="stylesheet">
<style>
:root{
  --orange:#f7a928;
  --green:#7dc242;
  --band:#8cc63f;
  --mint:#f1fbe2;
  --slate:#3f4b54;
  --text:#555;
  --dark:#111214;
  --gray-btn:#5d6870;
  --copy:#55585b;
}
*{margin:0;padding:0;box-sizing:border-box}
html,body{width:1200px;height:3975px;overflow:hidden}
body{position:relative;font-family:'Lato',sans-serif;color:var(--text);background:#fff}
.abs{position:absolute}
.display{font-family:'Michroma',sans-serif;text-transform:uppercase;color:var(--slate);letter-spacing:2px}
.btn{position:absolute;display:flex;align-items:center;justify-content:center;background:var(--orange);color:#fff;font-size:14px;border-radius:4px}

/* hero */
.hero{position:absolute;left:0;top:0;width:1200px;height:685px;overflow:hidden}
.hero-photo{position:absolute;inset:0;background:linear-gradient(180deg,#3f4d3a 0%,#4f6440 45%,#5d7a45 75%,#6b8a4c 100%)}
.site-header{position:absolute;left:0;top:0;width:1200px;height:110px;z-index:2}
.brand{left:111px;top:36px;display:flex;align-items:center;gap:14px;color:#fff;font-weight:700;font-size:30px;line-height:1}
.brand .mark{width:40px;height:40px;border:3px solid #fff;flex:none}
.nav{left:534px;top:57px;display:flex;gap:30px;color:#fff;font-size:15px;line-height:18px}
.hero-copy{position:absolute;inset:0;z-index:1}
.hero-copy h2{position:absolute;left:0;width:1200px;top:222px;text-align:center;color:#fff;font-weight:400;font-size:46px;line-height:56px}
.hero-copy h1{position:absolute;left:0;width:1200px;top:296px;text-align:center;color:#fff;font-size:58px;line-height:70px;letter-spacing:3px}
.hero-copy p{position:absolute;left:260px;width:680px;top:380px;text-align:center;color:#fff;font-size:22px;line-height:31px}
.dots{left:556px;top:623px;display:flex;gap:8px}
.dots span{width:11px;height:11px;background:#fff;border-radius:2px}
.dots span.on{width:37px;background:var(--orange)}

/* services */
.services{position:absolute;left:0;top:685px;width:1200px;height:570px;background:var(--mint)}
.svc-title{left:111px;top:85px;font-size:44px;line-height:55px}
.svc-intro{left:534px;top:78px;width:560px;font-size:19px;line-height:30px}
.svc{position:absolute;top:233px;width:200px}
.svc .ico{width:80px;height:80px;background:#d6efb8;border-radius:6px}
.svc h3{color:var(--green);font-size:21px;font-weight:400;margin-top:22px}
.svc p{font-size:14.5px;line-height:22px;margin-top:12px}
.svc .go{margin-top:12px}
.circle-arrow{position:absolute;width:36px;height:36px}

/* who */
.who-img{left:111px;top:1343px;width:455px;height:454px;background:linear-gradient(135deg,#3e6a2c,#6f9a48 55%,#a8c28a)}
.who h2{left:643px;top:1340px;font-size:42px}
.who p{position:absolute;left:643px;width:430px;font-size:15.5px;line-height:26px}

/* why */
.why-title{left:0;width:1200px;top:1872px;text-align:center;font-size:44px}
.why{position:absolute;top:1966px;width:190px;text-align:center;color:var(--green);font-size:20px;line-height:26px}
.why svg{display:block;margin:0 auto 20px}
.why.faded{opacity:.35}

/* cta */
.cta{position:absolute;left:0;top:2221px;width:1200px;height:428px;background:var(--band)}
.cta h2{position:absolute;left:0;width:1200px;top:97px;text-align:center;color:#fff;font-size:44px;line-height:54px}
.cta .btn{background:var(--gray-btn)}
.cta .tree{left:985px;top:160px;width:180px;height:250px;border-radius:50% 50% 8px 8px;background:rgba(255,255,255,.14)}

/* blog */
.blog-title{left:0;width:1200px;top:2725px;text-align:center;font-size:44px}
.card{position:absolute;top:2827px;width:304px}
.card .pic{height:199px}
.card h3{color:var(--green);font-size:22px;font-weight:400;line-height:31px;margin-top:38px}
.card p{font-size:14px;line-height:22px;margin-top:17px}
.card .more{color:var(--orange);font-size:14px;margin-top:22px}

/* footer */
.footer{position:absolute;left:0;top:3334px;width:1200px;height:583px;background:var(--dark);color:#fff}
.footer h2{position:absolute;left:113px;top:56px;font-family:'Oswald',sans-serif;font-weight:500;font-size:30px}
.footer .lead{position:absolute;left:113px;top:104px;font-size:12.5px;line-height:20px;font-weight:700}
.field{position:absolute;top:68px;height:46px;border:1px solid #ccc;border-radius:3px;font-size:12.5px;display:flex;align-items:center;justify-content:space-between;padding:0 18px}
.rule{position:absolute;left:111px;top:187px;width:978px;height:1px;background:#333}
.col{position:absolute;top:258px}
.col h4{font-family:'Oswald',sans-serif;font-weight:500;font-size:21px}
.col .bar{margin-top:8px;width:90px;height:2px;background:linear-gradient(90deg,#fff 0 80%,transparent 80%)}
.col ul{list-style:none;margin-top:24px}
.col li{font-size:14.5px;height:36px;display:flex;gap:16px}
.col li::before{content:"›";color:var(--green);font-size:18px;line-height:16px}
.col.plain li::before{content:none}
.col.plain li{height:46px}
.copy{position:absolute;left:0;top:3917px;width:1200px;height:58px;background:var(--copy);color:#fff;font-size:13px;text-align:center;line-height:58px}
</style>
</head>
<body>

<section class="hero">
  <div class="hero-photo" role="img" aria-label="Photo of an arborist tending a garden lawn and hedges"></div>
  <header class="site-header">
    <div class="abs brand"><span class="mark"></span>Verdell Tree Care</div>
    <nav class="abs nav"><span>Home</span><span>About</span><span>Services</span><span>Blog</span><span>Contact</span></nav>
    <div class="btn" style="left:925px;top:44px;width:162px;height:42px">Get A Quote</div>
  </header>
  <div class="hero-copy">
    <h2>Welcome To</h2>
    <h1 class="display">Verdell Tree Care</h1>
    <p>At Verdell Tree Care, we are more than just a tree service company, we are stewards of our beautiful trees.</p>
    <div class="btn" style="left:518px;top:464px;width:164px;height:41px">Contact Us</div>
    <div class="abs dots"><span class="on"></span><span></span><span></span><span></span></div>
  </div>
</section>

<section class="services">
  <h2 class="abs display svc-title">Our<br>Services</h2>
  <p class="abs svc-intro">Lorem ipsum dolor sit amet, consectetur adipiscing elit, sed do eiusmod tempor incididunt ut labore et dolore magna aliqua. Quis ipsum suspendisse ultrices gravida. Risus commodo viverra maecenas accumsan lacus vel facilisis.</p>
  <svg class="circle-arrow" style="left:50px;top:335px" viewBox="0 0 36 36"><circle cx="18" cy="18" r="18" fill="#c9cdc4"/><path d="M21 10l-8 8 8 8M13 18h12" stroke="#fff" stroke-width="4" fill="none"/></svg>
  <svg class="circle-arrow" style="left:1113px;top:335px" viewBox="0 0 36 36"><circle cx="18" cy="18" r="18" fill="#3f4b54"/><path d="M15 10l8 8-8 8M23 18H11" stroke="#fff" stroke-width="4" fill="none"/></svg>
  <div class="svc" style="left:111px"><div class="ico" role="img" aria-label="Icon of a worker pruning a tree"></div><h3>Tree Pruning</h3><p>Ut enim ad minim veniam, quis nostrud exercitation ullamco laboris nisi ut aliquip ex ea commodo consequat.</p><svg class="go" width="22" height="20" viewBox="0 0 22 20"><path d="M10 2l8 8-8 8M18 10H2" stroke="#7dc242" stroke-width="4" fill="none"/></svg></div>
  <div class="svc" style="left:372px"><div class="ico" role="img" aria-label="Icon of trees being removed"></div><h3>Tree Removal</h3><p>Excepteur sint occaecat aute irure cupidatat non proident, deserunt mollit anim id laborum."</p><svg class="go" width="22" height="20" viewBox="0 0 22 20"><path d="M10 2l8 8-8 8M18 10H2" stroke="#7dc242" stroke-width="4" fill="none"/></svg></div>
  <div class="svc" style="left:633px"><div class="ico" role="img" aria-label="Icon of a hand holding a young tree"></div><h3>Tree Preservation</h3><p>Ut enim ad minim veniam, quis nostrud exercitation ullamco laboris nisi ut aliquip ex ea commodo consequat.</p><svg class="go" width="22" height="20" viewBox="0 0 22 20"><path d="M10 2l8 8-8 8M18 10H2" stroke="#7dc242" stroke-width="4" fill="none"/></svg></div>
  <div class="svc" style="left:894px"><div class="ico" role="img" aria-label="Icon of a stump grinding machine"></div><h3>Stump grinding</h3><p>Excepteur sint occaecat aute irure cupidatat non proident, deserunt mollit anim id laborum."</p><svg class="go" width="22" height="20" viewBox="0 0 22 20"><path d="M10 2l8 8-8 8M18 10H2" stroke="#7dc242" stroke-width="4" fill="none"/></svg></div>
</section>

<section class="who">
  <div class="abs who-img" role="img" aria-label="Photo of an arborist trimming branches with loppers"></div>
  <h2 class="abs display">Who We Are</h2>
  <p style="top:1424px">At Verdell Tree Care, we are more than just a tree service company, we are stewards of our beautiful trees. With a passion deeply rooted in arboriculture, we embark on a mission to promote the health, beauty, and safety of your trees and landscapes.</p>
  <p style="top:1578px">Whether it's expert tree trimming to enhance aesthetics, meticulous tree removal to mitigate hazards, or comprehensive tree health assessments to ensure safety, we approach each task with unwavering dedication and attention to detail.</p>
  <div class="btn" style="left:643px;top:1752px;width:164px;height:41px">Read More</div>
</section>

<h2 class="abs display why-title">Why Choose Us?</h2>
<div class="why faded" style="left:-52px"><svg width="100" height="100" viewBox="0 0 100 100"><rect x="10" y="14" width="80" height="72" rx="4" fill="none" stroke="#3f4b54" stroke-width="3"/></svg>Licensed and Insured</div>
<div class="why" style="left:144px"><svg width="100" height="100" viewBox="0 0 100 100"><circle cx="50" cy="50" r="46" fill="none" stroke="#3f4b54" stroke-width="4" stroke-dasharray="200 30"/><text x="50" y="60" text-anchor="middle" font-family="Lato,sans-serif" font-weight="700" font-size="28" fill="#3f4b54">24/7</text></svg>24-Hours<br>Emergency Services</div>
<div class="why" style="left:363px"><svg width="100" height="100" viewBox="0 0 100 100"><path d="M50 88C30 60 24 48 24 36a26 26 0 0 1 52 0c0 12-6 24-26 52z" fill="none" stroke="#3f4b54" stroke-width="4"/><circle cx="50" cy="36" r="10" fill="none" stroke="#3f4b54" stroke-width="4"/><ellipse cx="50" cy="90" rx="38" ry="7" fill="none" stroke="#3f4b54" stroke-width="3"/></svg>Locally Owned &amp;<br>Operated</div>
<div class="why" style="left:545px"><svg width="100" height="100" viewBox="0 0 100 100"><circle cx="46" cy="38" r="16" fill="none" stroke="#3f4b54" stroke-width="4"/><path d="M14 90c0-18 14-30 32-30s32 12 32 30" fill="none" stroke="#3f4b54" stroke-width="4"/><path d="M66 62l14 5v10c0 8-6 12-14 15" fill="none" stroke="#3f4b54" stroke-width="3"/></svg>Professional<br>Work</div>
<div class="why" style="left:711px"><svg width="100" height="100" viewBox="0 0 100 100"><path d="M50 6l34 12v28c0 24-16 40-34 48C32 86 16 70 16 46V18z" fill="none" stroke="#3f4b54" stroke-width="4"/><path d="M36 50l10 10 20-20" fill="none" stroke="#3f4b54" stroke-width="5"/></svg>Safety is Our<br>No.1 Priority</div>
<div class="why" style="left:887px"><svg width="100" height="100" viewBox="0 0 100 100"><rect x="22" y="8" width="56" height="82" rx="4" fill="none" stroke="#3f4b54" stroke-width="4"/><path d="M32 50h36M32 62h26M32 74h26" stroke="#3f4b54" stroke-width="3"/><circle cx="72" cy="70" r="12" fill="#fff" stroke="#3f4b54" stroke-width="3"/><path d="M66 64l12 12M78 64L66 76" stroke="#3f4b54" stroke-width="3"/></svg>Free Estimates</div>
<div class="why faded" style="left:1061px"><svg width="100" height="100" viewBox="0 0 100 100"><rect x="8" y="20" width="84" height="60" rx="4" fill="none" stroke="#3f4b54" stroke-width="3"/><circle cx="32" cy="46" r="10" fill="none" stroke="#3f4b54" stroke-width="3"/></svg>Licensed<br>Arborist on Staff</div>

<section class="cta">
  <div class="abs tree" role="img" aria-label="Line drawing of a leafy tree"></div>
  <h2 class="display">Schedule an appointment<br>to meet or email us<br>your questions</h2>
  <div class="btn" style="left:518px;top:280px;width:164px;height:44px">Contact Us</div>
</section>

<h2 class="abs display blog-title">Our Blog</h2>
<svg class="circle-arrow" style="left:58px;top:2919px;width:28px;height:28px" viewBox="0 0 36 36"><circle cx="18" cy="18" r="18" fill="#3f4b54"/><path d="M21 10l-8 8 8 8M13 18h12" stroke="#fff" stroke-width="4" fill="none"/></svg>
<svg class="circle-arrow" style="left:1114px;top:2919px;width:28px;height:28px" viewBox="0 0 36 36"><circle cx="18" cy="18" r="18" fill="#3f4b54"/><path d="M15 10l8 8-8 8M23 18H11" stroke="#fff" stroke-width="4" fill="none"/></svg>
<article class="card" style="left:111px"><div class="pic" role="img" aria-label="Photo of a fallen tree in a front yard" style="background:linear-gradient(180deg,#9fb39a,#4f7a37)"></div><h3>Lorem ipsum dolor sit amet, consectetur adipiscing</h3><p>Sed ut perspiciatis unde omnis iste natus error dantium, totam rem aperiam, eaque ipsa quae ab illo inventore veritatis et quasi architecto beatae vitae dicta sunt explicabo.</p><div class="more">Read More ...</div></article>
<article class="card" style="left:448px"><div class="pic" role="img" aria-label="Photo of a stump grinder at work" style="background:linear-gradient(160deg,#6d5a3a,#d8a630 50%,#4a3b2a)"></div><h3>Lorem ipsum dolor sit amet, consectetur adipiscing</h3><p>Sed ut perspiciatis unde omnis iste natus error dantium, totam rem aperiam, eaque ipsa quae ab illo inventore veritatis et quasi architecto beatae vitae dicta sunt explicabo.</p><div class="more">Read More ...</div></article>
<article class="card" style="left:784px"><div class="pic" role="img" aria-label="Photo of a climber cutting a large tree" style="background:linear-gradient(180deg,#b8bfb4,#5c5f4e)"></div><h3>Lorem ipsum dolor sit amet, consectetur adipiscing</h3><p>Sed ut perspiciatis unde omnis iste natus error dantium, totam rem aperiam, eaque ipsa quae ab illo inventore veritatis et quasi architecto beatae vitae dicta sunt explicabo.</p><div class="more">Read More ...</div></article>

<footer class="footer">
  <h2>Contact Us</h2>
  <p class="lead">Excepteur sint occaecat cupidatat non proident,<br>culpa qui officia deserunt mollit laborum.</p>
  <div class="field" style="left:466px;width:239px">Name<svg width="12" height="14" viewBox="0 0 12 14"><rect x="1" y="6" width="10" height="7" fill="none" stroke="#7dc242"/><path d="M3 6V4a3 3 0 0 1 6 0v2" fill="none" stroke="#7dc242"/></svg></div>
  <div class="field" style="left:716px;width:237px">Email Address<svg width="14" height="10" viewBox="0 0 14 10"><rect x="1" y="1" width="12" height="8" fill="none" stroke="#7dc242"/><path d="M1 1l6 5 6-5" fill="none" stroke="#7dc242"/></svg></div>
  <div class="btn" style="left:965px;top:68px;width:124px;height:46px;background:var(--band)">Subscribe</div>
  <div class="rule"></div>
  <div class="col plain" style="left:113px"><h4>Contact Info</h4><div class="bar"></div><ul><li>(555) 014-2290</li><li>(555) 017-4831</li><li>hello@verdelltrees.example</li></ul></div>
  <div class="col" style="left:401px"><h4>Quick Links</h4><div class="bar"></div><ul><li>Home</li><li>About</li><li>Services</li><li>Blog</li><li>Contact</li></ul></div>
  <div class="col" style="left:665px"><h4>Other Links</h4><div class="bar"></div><ul><li>Support</li><li>Terms and Conditions</li><li>Privacy policy</li><li>Cookies Policy</li><li>Copyright Notification</li></ul></div>
  <div class="col" style="left:978px"><h4>Follow Us</h4><div class="bar"></div><ul><li>Photo Stream</li><li>Pro Network</li><li>Community Page</li><li>Video Channel</li><li>Short Posts</li></ul></div>
</footer>
<div class="copy">Copyright © 2024 Verdell Tree Care. All rights reserved.</div>

</body>
</html>
```